Hip / Cool Business Card for Custom Accessory Company

I would like to get a 2 sided design for standard size business cards, glossy (2 inches x 3.5 inches). Can be landscape or portrait layout! The design should include our logo (attached). The card should be extremely clear that the company is Tidy Pebble. Should also have our URL clear. Should also use the color scheme seen on our upcoming site, tidypebble.example. The font we use is called "hurry up." Other than that, please go-to-town. We are targeting 15-45 y.o. market, with a skew on the 20-30 crowd. We do custom and stock iPhone cases as well as Cufflinks, Winestoppers; see the website for more.
Updates

Project Deadline Extended
Reason: Extending in case the US July 4th Holiday is keeping people from working!!

Industry/Entity Type

Landscape

Requirements
Must have
• Must be clear that the website is tidypebble.example. Must be clear that custom designs are an option.
Nice to have
• images of our designs. examples of our designs.
Should not have
• hard on the eyes contrasting colors such as orange on black. green on blue. Should not have any fonts that are considered "old" like Times New Roman. But decorative fonts are fine.

```html
<!DOCTYPE html>
<html lang="en">
<head>
<meta charset="utf-8">
<title>Tidy Pebble Business Cards</title>
<link rel="stylesheet" href="https://fonts.googleapis.com/css2?family=Open+Sans:wght@400;600;800&display=swap">
<style>
  :root {
    --stage: #3a3a3d;
    --card-white: #f7f7f7;
    --ink: #111111;
    --teal: #1f9ba3;
    --muted: #bdbdbd;
    --light: #ffffff;
  }
  * { box-sizing: border-box; margin: 0; padding: 0; }
  html, body {
    width: 1200px; height: 925px; overflow: hidden;
    background: var(--stage);
    font-family: "Open Sans", sans-serif;
  }
  .canvas { position: relative; width: 1200px; height: 925px; }
  .card {
    position: absolute; top: 314px;
    width: 520px; height: 297px;
    background: linear-gradient(135deg, #ffffff 0%, var(--card-white) 60%, #e6e6e6 100%);
    box-shadow: 0 10px 28px rgba(0,0,0,.35);
    overflow: hidden;
  }
  .card--front { left: 60px; }
  .card--back { left: 620px; }

  .brand { position: absolute; display: flex; align-items: center; gap: 10px; }
  .brand__dot { border-radius: 50%; background: var(--teal); flex: none; }
  .brand__text { display: flex; flex-direction: column; }
  .brand__name {
    font-weight: 800; color: var(--ink); text-transform: uppercase;
    letter-spacing: 1px; white-space: nowrap; line-height: 1.1;
  }
  .brand__tagline {
    font-size: 10px; font-weight: 600; color: var(--ink);
    letter-spacing: .5px; margin-top: 3px; white-space: nowrap;
  }
  .card--front .brand { left: 50%; top: 50%; transform: translate(-50%, -50%); }
  .card--front .brand__dot { width: 52px; height: 52px; }
  .card--front .brand__name { font-size: 34px; }

  .card--back .brand { left: 24px; top: 150px; gap: 8px; }
  .card--back .brand__dot { width: 28px; height: 28px; }
  .card--back .brand__name { font-size: 18px; }

  .back-shape { position: absolute; inset: 0; }

  .person { position: absolute; left: 318px; top: 34px; color: var(--light); }
  .person__name { font-size: 18px; font-weight: 600; }
  .person__title { font-size: 12px; color: var(--muted); margin-top: 2px; }

  .contacts {
    position: absolute; left: 318px; top: 150px;
    list-style: none; color: var(--light); font-size: 9.5px; line-height: 1.25;
  }
  .contacts li { display: flex; align-items: flex-start; gap: 6px; margin-bottom: 5px; }
  .contacts svg { width: 11px; height: 11px; flex: none; margin-top: 1px; }
</style>
</head>
<body>
<main class="canvas">

  <section class="card card--front" aria-label="Card front">
    <div class="brand">
      <span class="brand__dot"></span>
      <span class="brand__name">Tidy Pebble</span>
    </div>
  </section>

  <section class="card card--back" aria-label="Card back">
    <svg class="back-shape" viewBox="0 0 520 297" preserveAspectRatio="none">
      <path d="M280 0 H520 V297 H222 Q200 140 280 0 Z" fill="var(--teal)"/>
      <path d="M294 0 H520 V297 H236 Q214 140 294 0 Z" fill="var(--ink)"/>
    </svg>

    <div class="brand">
      <span class="brand__dot"></span>
      <span class="brand__text">
        <span class="brand__name">Tidy Pebble</span>
        <span class="brand__tagline">Custom &amp; stock designs</span>
      </span>
    </div>

    <div class="person">
      <p class="person__name">Alex Moreno</p>
      <p class="person__title">Owner / C.E.O</p>
    </div>

    <ul class="contacts">
      <li>
        <svg viewBox="0 0 12 12"><circle cx="6" cy="6" r="6" fill="#fff"/><path d="M6 2.5a2 2 0 0 0-2 2c0 1.6 2 4.5 2 4.5s2-2.9 2-4.5a2 2 0 0 0-2-2z" fill="#111"/></svg>
        <span>Unit 4, Elm Court<br>CA 90412</span>
      </li>
      <li>
        <svg viewBox="0 0 12 12"><circle cx="6" cy="6" r="6" fill="#fff"/><path d="M4 3l1.2 1.6-.7.8a4 4 0 0 0 2.1 2.1l.8-.7L9 8l-.6 1A4.8 4.8 0 0 1 3 3.6z" fill="#111"/></svg>
        <span>555-201-3344</span>
      </li>
      <li>
        <svg viewBox="0 0 12 12"><circle cx="6" cy="6" r="6" fill="#fff"/><path d="M4 3l1.2 1.6-.7.8a4 4 0 0 0 2.1 2.1l.8-.7L9 8l-.6 1A4.8 4.8 0 0 1 3 3.6z" fill="#111"/></svg>
        <span>555-874-1902</span>
      </li>
      <li>
        <svg viewBox="0 0 12 12"><circle cx="6" cy="6" r="6" fill="#fff"/><rect x="3" y="3" width="6" height="6" rx="1" fill="#111"/></svg>
        <span>555-310-6628</span>
      </li>
      <li>
        <svg viewBox="0 0 12 12"><circle cx="6" cy="6" r="6" fill="#fff"/><rect x="2.8" y="3.8" width="6.4" height="4.4" fill="#111"/><path d="M2.8 3.8L6 6.4l3.2-2.6" stroke="#fff" stroke-width=".7" fill="none"/></svg>
        <span>hello@tidypebble.example</span>
      </li>
      <li>
        <svg viewBox="0 0 12 12"><circle cx="6" cy="6" r="6" fill="#fff"/><circle cx="6" cy="6" r="3.2" fill="none" stroke="#111" stroke-width=".9"/><path d="M2.8 6h6.4M6 2.8v6.4" stroke="#111" stroke-width=".7"/></svg>
        <span>www.tidypebble.example</span>
      </li>
    </ul>
  </section>

</main>
</body>
</html>
```